Professional and creative business card design for recruiting service providers

Our company supports German medium-sized companies in filling vacancies promptly. For this we use social media marketing and bring our customers into the visibility.

We want a professional but also creative design for our business cards.

Please look at lindqvar-staff.de to get an impression of our CI.

Target Market(s)

Small and medium-sized companies in Germany from the industry

Industry/Entity Type

Industrie, Handwerk

Contact Information for Business Card

Name, Position, Telefonnummer, Email, Website

Colors
EE7325
F08F49
F5BC92
FAE3D3
FDF4ED

Requirements
Must have
• A picture of the employee and in the style of www.lindqvar-staff.de

```html
<!DOCTYPE html>
<html lang="de">
<head>
<meta charset="utf-8">
<title>Lindqvar &amp; Staff – Visitenkarte</title>
<link href="https://fonts.googleapis.com/css2?family=Montserrat:wght@700&family=Arimo:wght@400;700&display=swap" rel="stylesheet">
<style>
  :root {
    --orange: #EE7325;
    --orange-soft: #F08F49;
    --ink: #2b2b2b;
    --card-dark: #2d2d2d;
    --paper: #ffffff;
    --stage: #e9e9e9;
    --muted: #cfcfcf;
  }
  * { box-sizing: border-box; margin: 0; padding: 0; }
  html, body { width: 1200px; height: 802px; overflow: hidden; }
  body { background: var(--stage); font-family: "Arimo", Arial, sans-serif; position: relative; }

  .card {
    position: absolute; top: 239px; width: 500px; height: 324px;
    overflow: hidden; box-shadow: 0 6px 18px rgba(0,0,0,.18);
  }
  .card--front { left: 60px; background: var(--paper); }
  .card--back { left: 640px; background: var(--card-dark); }

  .brand {
    display: flex; align-items: center; gap: 10px;
    font-family: "Montserrat", Arial, sans-serif; font-weight: 700;
    text-transform: uppercase; letter-spacing: 1.5px; line-height: 1.05;
  }
  .brand__square { width: 22px; height: 22px; background: var(--orange); flex: none; }
  .brand--front { position: absolute; left: 28px; top: 34px; color: var(--ink); font-size: 21px; }
  .brand--back {
    position: absolute; right: 44px; top: 50%; transform: translateY(-50%);
    color: var(--paper); font-size: 22px; background: var(--card-dark); padding: 12px 14px;
  }

  .person { position: absolute; left: 28px; top: 124px; }
  .person__name { color: var(--orange); font-weight: 700; font-size: 19px; text-transform: uppercase; letter-spacing: .5px; }
  .person__role { color: var(--ink); font-size: 14px; margin-top: 3px; }

  .address { position: absolute; left: 28px; top: 188px; color: var(--ink); font-size: 13px; line-height: 1.35; font-style: normal; }

  .contact { position: absolute; left: 28px; top: 240px; list-style: none; color: var(--ink); font-size: 13px; line-height: 1.45; }
  .contact li { display: flex; align-items: center; gap: 8px; }
  .contact svg { width: 12px; height: 12px; flex: none; }

  .portrait {
    position: absolute; right: 0; top: 0; width: 230px; height: 324px;
    background: linear-gradient(180deg, #f1f1f1 0%, #c9c9c9 30%, #3a3a3f 55%, #1c1c22 100%);
  }

  .pattern {
    position: absolute; inset: 0;
    background: linear-gradient(135deg, #1f1f1f 0%, #2e2e2e 45%, #5a5a5a 75%, #3a3a3a 100%);
  }
</style>
</head>
<body>

  <section class="card card--front" aria-label="Visitenkarte Vorderseite">
    <div class="brand brand--front">
      <span class="brand__square"></span>
      <span>Lindqvar<br>&amp; Staff</span>
    </div>

    <div class="person">
      <p class="person__name">Tobias Renner</p>
      <p class="person__role">Manager</p>
    </div>

    <address class="address">
      Kornbergstraße 27c<br>
      70176 Stuttgart
    </address>

    <ul class="contact">
      <li>
        <svg viewBox="0 0 24 24" aria-hidden="true"><path fill="var(--orange)" d="M6.6 10.8a15 15 0 0 0 6.6 6.6l2.2-2.2a1 1 0 0 1 1-.25 11.4 11.4 0 0 0 3.6.57 1 1 0 0 1 1 1V20a1 1 0 0 1-1 1A17 17 0 0 1 3 4a1 1 0 0 1 1-1h3.5a1 1 0 0 1 1 1c0 1.25.2 2.45.57 3.57a1 1 0 0 1-.25 1z"/></svg>
        0160 473 2951
      </li>
      <li>
        <svg viewBox="0 0 24 24" aria-hidden="true"><rect x="2.5" y="5" width="19" height="14" rx="1.5" fill="none" stroke="var(--orange)" stroke-width="2.2"/><path d="M3 6l9 7 9-7" fill="none" stroke="var(--orange)" stroke-width="2.2"/></svg>
        info@lindqvar-staff.de
      </li>
      <li>
        <svg viewBox="0 0 24 24" aria-hidden="true"><circle cx="12" cy="12" r="9.5" fill="none" stroke="var(--orange)" stroke-width="2.2"/><path d="M2.5 12h19M12 2.5c3 3 3 16 0 19M12 2.5c-3 3-3 16 0 19" fill="none" stroke="var(--orange)" stroke-width="1.8"/></svg>
        www.lindqvar-staff.de
      </li>
    </ul>

    <div class="portrait" role="img" aria-label="Porträtfoto des Mitarbeiters in dunklem Sakko und Rollkragenpullover"></div>
  </section>

  <section class="card card--back" aria-label="Visitenkarte Rückseite">
    <div class="pattern" role="img" aria-label="Geprägtes dunkles Wiederholungsmuster über die gesamte Fläche"></div>
    <div class="brand brand--back">
      <span class="brand__square"></span>
      <span>Lindqvar<br>&amp; Staff</span>
    </div>
  </section>

</body>
</html>
```